Venture Capital Investment Firm

We are looking to overhaul our existing website (substantially), with only using the same logos (which we can provide).
We are an investment firm that focuses on making loans to late stage technology companies. Our site should ultimately look like other venture capital firms, and look modern and fresh. We have an existing website www.norvellhub.com which this will be replacing, although we will be using a lot of the existing written content, and potentially the numbers of pages we will need, we are not wed to anything else. Please feel free to shoot any questions at any time and thank you in advance for your help!
Websites we like as examples:
https://www.tesmarkfund.com/
https://www.brindlewoodpartners.com/
Target Market(s)
Potential investors who will invest in our firm, as well as potentially companies that are looking to borrow money from us.
Coding
Coded - Design and coding required
Number of Pages Required
5+ page
Colors
Designer to choose colors to be used in the design.
Look and feel

```html
<!DOCTYPE html>
<html lang="en">
<head>
<meta charset="utf-8">
<title>Norvell Hub Investment Partners</title>
<link href="https://fonts.googleapis.com/css2?family=Lato:wght@400;700;900&display=swap" rel="stylesheet">
<style>
:root{
  --navy:#14143f;
  --gold:#b08d26;
  --grey-bg:#f1f1f1;
  --text:#444;
  --white:#fff;
  --footer:#1b1b1b;
}
*{margin:0;padding:0;box-sizing:border-box}
html,body{width:1200px;height:3223px;overflow:hidden;background:#fff}
body{font-family:'Lato',sans-serif;color:var(--text);position:relative}
section,header,footer{position:relative;width:1200px}
.btn{display:inline-block;background:var(--gold);color:#fff;font-weight:700;text-transform:uppercase;text-align:center;font-size:16px}
h2.section-title{font-weight:700;color:var(--navy);font-size:43px;text-align:center;position:absolute;left:0;width:100%}
.notch{position:absolute;left:560px;width:0;height:0;border-left:40px solid transparent;border-right:40px solid transparent}

/* header */
.site-header{height:132px}
.brand{position:absolute;left:74px;top:38px;display:flex;align-items:center;gap:14px}
.brand-dot{width:46px;height:46px;border-radius:50%;background:var(--navy)}
.brand-name{font-size:34px;font-weight:700;color:var(--navy);letter-spacing:1px}
.main-nav{position:absolute;top:49px;left:400px;display:flex;font-size:14px;font-weight:700;color:#222}
.main-nav a{padding:10px 0;margin-right:50px;text-decoration:none;color:#222}
.main-nav a.active{border:2px solid var(--navy);color:var(--gold);padding:9px 18px;margin-right:32px}

/* hero */
.hero{height:582px;background:linear-gradient(120deg,#8d8a86 0%,#b7b3ae 35%,#6f6a63 70%,#3f3a34 100%)}
.hero-content{position:absolute;top:0;left:0;width:100%;text-align:center;color:#fff}
.hero h1{position:absolute;top:170px;width:100%;font-size:82px;font-weight:900;letter-spacing:1px}
.hero p{position:absolute;top:272px;width:100%;font-size:22px;line-height:34px;text-transform:uppercase;font-weight:700}
.hero .btn{position:absolute;top:362px;left:420px;width:361px;height:52px;line-height:52px;font-size:17px;font-weight:400}
.dots{position:absolute;display:flex;gap:13px}
.dots span{width:15px;height:15px;border-radius:50%;background:var(--navy)}
.hero .dots{top:515px;left:549px}
.hero .dots span:first-child{background:#fff}

/* welcome */
.welcome{height:426px}
.welcome h2{top:85px}
.welcome p{position:absolute;top:150px;left:120px;width:960px;text-align:center;font-size:16px;line-height:29.5px}
.welcome .btn{position:absolute;top:299px;left:510px;width:179px;height:53px;line-height:53px}

/* strategy */
.strategy{height:480px;background:var(--grey-bg)}
.strategy h2{top:68px}
.strategy .notch{top:0;border-top:20px solid #fff}
.pillar{position:absolute;top:170px;width:340px;text-align:center}
.pillar svg{display:block;margin:0 auto}
.pillar h3{font-size:24px;font-weight:700;color:var(--navy);margin-top:20px}
.pillar p{font-size:14px;line-height:27px;margin-top:12px;color:#444}
.divider{position:absolute;top:170px;width:1px;height:225px;background:#ccc}

/* team */
.team{height:580px}
.team h2{top:50px}
.member{position:absolute;top:150px;width:280px;text-align:center}
.portrait{width:186px;height:186px;border-radius:50%;margin:0 auto;border:6px solid #c8c8c8;background:radial-gradient(circle at 50% 40%,#6e6e6e,#1e1e1e)}
.member h3{font-size:25px;font-weight:700;color:var(--navy);margin-top:38px}
.member .role{font-size:15px;margin-top:14px}
.member .btn{margin-top:30px;width:140px;height:43px;line-height:43px;font-size:15px}

/* news */
.news{height:482px;background:var(--grey-bg)}
.news .notch{top:0;border-top:20px solid #fff}
.news h2{top:68px}
.news-item{position:absolute;top:148px;width:330px}
.news-item .tag{color:var(--gold);font-size:17px;font-weight:700}
.news-item h3{color:var(--navy);font-size:19px;line-height:28px;font-weight:700;margin-top:10px}
.news-item p{font-size:14px;line-height:26px;margin-top:6px}
.news-item .date{color:var(--navy);font-weight:700;font-size:15px;margin-top:13px}
.news .dots{top:413px;left:570px;gap:12px}
.news .dots span{width:12px;height:12px;background:#888}
.news .dots span:first-child{background:var(--navy)}

/* contact */
.contact{height:451px;background:linear-gradient(135deg,#5a5d80 0%,#4b4e72 50%,#3b3d5e 100%)}
.contact h2{top:45px;color:#fff}
.field{position:absolute;background:#fff;height:41px;font-size:13px;color:#333;padding:12px 12px}
.field.select::after{content:"⬍";position:absolute;right:14px;top:11px;font-size:13px}
.contact .btn{position:absolute;top:331px;left:75px;width:179px;height:52px;line-height:52px;font-size:17px}
.info{position:absolute;left:614px;color:#fff;font-size:15px;display:flex;align-items:center;gap:12px}
.info svg{flex:none}
.map{position:absolute;left:614px;top:195px;width:512px;height:189px;border:6px solid #b5b5b8;background:linear-gradient(90deg,#5c5c5c 0%,#5c5c5c 28%,#e5e5e5 30%,#e5e5e5 55%,#5c5c5c 58%,#5c5c5c 70%,#e0e0e0 73%)}

/* footer */
.site-footer{height:90px;background:var(--footer)}
.site-footer small{position:absolute;left:74px;top:39px;color:#ddd;font-size:12px}
.social{position:absolute;right:84px;top:35px;display:flex;gap:20px}
.social span{width:20px;height:20px;border-radius:50%;background:#fff}
</style>
</head>
<body>

<header class="site-header">
  <div class="brand"><span class="brand-dot"></span><span class="brand-name">NORVELL HUB</span></div>
  <nav class="main-nav">
    <a class="active" href="#">HOME</a><a href="#">STRATEGY</a><a href="#">ABOUT US</a><a href="#">TEAM</a><a href="#">NEWS</a><a href="#">CONTACT</a><a href="#">INVESTORS</a>
  </nav>
</header>

<section class="hero" role="img" aria-label="Photo of business people reviewing financial charts on a laptop">
  <div class="hero-content">
    <h1>NORVELLHUB</h1>
    <p>We are a global structured credit investment firm focused on<br>the healthcare and technology industries</p>
    <a class="btn" href="#">Learn more about our strategy</a>
    <div class="dots"><span></span><span></span><span></span><span></span></div>
  </div>
</section>

<section class="welcome">
  <div class="notch" style="top:0;border-top:22px solid #7a756f"></div>
  <h2 class="section-title">Welcome to Norvellhub</h2>
  <p>Norvell Hub is a private investment firm unique in its dual focus on life science and technology credit opportunities.&nbsp; Our ambidextrous approach to investing reflects a broad recognition and appreciation for the critical role intellectual property plays in the successful commercialization of products.&nbsp; We apply our extensive industry expertise to assess the revenue visibility created by these assets and offer a range of creative financing solutions.</p>
  <a class="btn" href="#">Read more</a>
</section>

<section class="strategy">
  <div class="notch"></div>
  <h2 class="section-title">Our Strategy</h2>
  <div class="pillar" style="left:64px">
    <svg width="68" height="62" viewBox="0 0 68 62"><path fill="#b08d26" d="M0 62V30l14 10V30l14 10V30l14 10V0h10v0h8V0h8v62z"/><g fill="#fff"><rect x="8" y="48" width="6" height="5"/><rect x="20" y="48" width="6" height="5"/><rect x="32" y="48" width="6" height="5"/><rect x="44" y="48" width="6" height="5"/></g></svg>
    <h3>Industry Focus</h3>
    <p>Our focus spans the life science and technology industries, two sectors where intellectual property (IP) is an integral driver of asset and enterprise value.</p>
  </div>
  <div class="divider" style="left:420px"></div>
  <div class="pillar" style="left:425px">
    <svg width="34" height="68" viewBox="0 0 34 68"><path fill="#b08d26" d="M17 22C10 10 2 12 0 6c8-2 15 2 17 12 2-10 9-14 17-12-2 6-10 4-17 16z"/><rect x="9" y="26" width="16" height="6" fill="#b08d26"/><path fill="#b08d26" d="M10 34h14v24a7 7 0 0 1-14 0z"/></svg>
    <h3>Life Sciences</h3>
    <p>We have a long track record of partnering with companies and investors that create and commercialize life science products with extensive experience.</p>
  </div>
  <div class="divider" style="left:780px"></div>
  <div class="pillar" style="left:790px">
    <svg width="88" height="62" viewBox="0 0 88 62"><rect x="6" y="0" width="76" height="50" rx="3" fill="#b08d26"/><rect x="12" y="6" width="64" height="38" fill="#f1f1f1"/><rect x="0" y="52" width="88" height="8" rx="2" fill="#b08d26"/><circle cx="36" cy="22" r="8" fill="#b08d26"/><circle cx="54" cy="28" r="6" fill="#b08d26"/><circle cx="36" cy="22" r="3" fill="#f1f1f1"/><circle cx="54" cy="28" r="2" fill="#f1f1f1"/></svg>
    <h3>Technology</h3>
    <p>We uniquely offer sizeable and flexible structured credit financing solutions to innovative technology companies with a focus on enterprise software.</p>
  </div>
</section>

<section class="team">
  <h2 class="section-title">Our Team</h2>
  <div class="member" style="left:100px"><div class="portrait" role="img" aria-label="Portrait of Martin Kessler"></div><h3>Martin Kessler</h3><div class="role">Managing Partner</div><a class="btn" href="#">Read more</a></div>
  <div class="member" style="left:461px"><div class="portrait" role="img" aria-label="Portrait of Devan Rao"></div><h3>Devan Rao</h3><div class="role">Managing Partner</div><a class="btn" href="#">Read more</a></div>
  <div class="member" style="left:820px"><div class="portrait" role="img" aria-label="Portrait of Owen Hartley"></div><h3>Owen Hartley</h3><div class="role">Partner</div><a class="btn" href="#">Read more</a></div>
</section>

<section class="news">
  <div class="notch"></div>
  <h2 class="section-title">Norvell Hub News</h2>
  <article class="news-item" style="left:74px"><div class="tag">Press Release</div><h3>Norvell Hub completes structured debt investment in Brightlane</h3><p>Norvell Hub Investment Partners (“Norvell Hub”) announced today that it has completed a structured debt investment in Brightlane, Inc.</p><div class="date">Novmeber 2019</div></article>
  <article class="news-item" style="left:434px"><div class="tag">Press Release</div><h3>Norvell Hub completes structured debt investment in Brightlane</h3><p>Norvell Hub Investment Partners (“Norvell Hub”) announced today that it has completed a structured debt investment in Brightlane, Inc.</p><div class="date">Novmeber 2019</div></article>
  <article class="news-item" style="left:795px"><div class="tag">Press Release</div><h3>Norvell Hub completes structured debt investment in Brightlane</h3><p>Norvell Hub Investment Partners (“Norvell Hub”) announced today that it has completed a structured debt investment in Brightlane, Inc.</p><div class="date">Novmeber 2019</div></article>
  <div class="dots"><span></span><span></span><span></span></div>
</section>

<section class="contact" role="img" aria-label="Background photo of a businessman in a suit, tinted blue">
  <h2 class="section-title">Contact Us</h2>
  <div class="field" style="left:75px;top:128px;width:248px">Name</div>
  <div class="field" style="left:339px;top:128px;width:248px">Email Address</div>
  <div class="field" style="left:75px;top:183px;width:248px">Phone No</div>
  <div class="field select" style="left:339px;top:183px;width:248px">Select Services</div>
  <div class="field" style="left:75px;top:241px;width:512px;height:75px">Description</div>
  <a class="btn" href="#">Submit</a>
  <div class="info" style="top:125px"><svg width="10" height="14" viewBox="0 0 10 14"><path fill="#fff" d="M5 0a5 5 0 0 1 5 5c0 4-5 9-5 9S0 9 0 5a5 5 0 0 1 5-5z"/><circle cx="5" cy="5" r="2" fill="#4b4e72"/></svg><span style="margin-left:12px">2250 Harlow Street #310 San Francisco, CA&nbsp; 94107</span></div>
  <div class="info" style="top:153px"><svg width="13" height="13" viewBox="0 0 13 13"><path fill="#fff" d="M2 0l3 3-2 2c1 2 3 4 5 5l2-2 3 3-2 2C5 13 0 8 0 2z"/></svg><span style="margin-left:8px">415-555-0148</span><svg style="margin-left:10px" width="15" height="11" viewBox="0 0 15 11"><rect width="15" height="11" fill="#fff"/><path d="M0 0l7.5 6L15 0" stroke="#4b4e72" fill="none"/></svg><span>hello@norvellhub.com</span></div>
  <div class="map" role="img" aria-label="Map of the San Francisco Bay Area with office location pin"></div>
</section>

<footer class="site-footer">
  <small>Copyright ©2019 Norvell Hub. All Rights Reserved.</small>
  <div class="social"><span></span><span></span><span></span><span></span><span></span></div>
</footer>

</body>
</html>
```